Packaging and labelling for Swiss made Organic CBD Oil

Visit our website www.clearleafmerida.example
We have not put any product on yet as require packaging and label design .
Website will give you a great feel for the company and how we have used
the logo . The Vextora cbd product shown is a company similar to ourselves with similar core values , we liked the clean packaging design they have .

Im happy if you want use the mandala symbol in our logo separate from
KELVORA, to separate and use the mandala symbol as a larger icon than
it appears in our logo
Clean , Pure , organic feel. Like the product to look pharmaceutical and life changing not gimmicky.
Colours to go with or be the same as our logo colours
But not too cold and clinical
Bottle size 84mm x 25mm
Label size 75mm x 30mm
Box 30mm x 30mm x 100mm
6 products
Full Spectrum :
500mg CBD (5%)
1000mg CBD ( 10% )
1500mg CBD (15%)
2000mg CBD ( 20% )
Broad spectrum THC Free
500mg CBD (5%)
Pets
500mg Broad Spectrum THC Free
Updates

Would like the design to be more modern than traditional

LABEL Information Front of Bottle - Logo KELVORA & Mandala - Mandala can be used separately as design symbol Organic Cannabis Oil 1500mg CBD (15%) Ful Spectrum 10ml Back of bottle Ingredients: Organic Cannabis Oil Extract Organic Sunflower Seed Oil THC - 0.2% Certified Swiss Organic Cultivation Shake well before use. Store in a cool , dry place and out of the each of children BOX information Front and rear Logo - KELVORA & Mandala - Mandala can be used separately as a design symbol Organic Cannabis Oil 1500mg CBD (15%) Full Spectrum Sides x 2 This product is a food supplement and is not intended to diagnose, treat, cure or prevent any disease If you are pregnant, lactating or taking any medication consult your health care practitioner Suitable for vegetarians and vegans Ingredients Organic Cannabis Oil extract Organis Sunflower Oil Store in a cool ,dry place, out of the reach of children Recommended Use 1-5 drops ( 1 drop = 7.5mg CBD ) Subject to body weight and personal requirement - visit www.clearleafmerida for more information 100% Natural 100% Organic GMO free 100% Vegan ( symbol with each ) Expiry date see bottle label Cultivated and manufactured in Switzerland

Target Market(s)

age 40 - 80

Font styles to use
Other font styles liked:
• In our website we have used Open Sans for the copy and Lato for headings .

Requirements
Must have
• look like an Industry leader
Kelvora will change the quality of peoples lives and in some cases may
even save lives so want look powerful and credible
Our Mission is - Through Delivering Pure , Premium , Organic products we will educate, inform and help people achieve healthier , happier lifestyles
Nice to have
• Colours to look good with our logo colours or be the same as our logo
colours
Logo Font - Avenir Black and Avenir Book

Font used in website - Content - Open Sans / Headings - Lato
If you have another font for the packaging information that will go well with
our logo, I'm happy for you to use your skills

```html
<!DOCTYPE html>
<html lang="en">
<head>
<meta charset="utf-8">
<title>Kelvora Organic Cannabis Oil – Front Label</title>
<link rel="stylesheet" href="https://fonts.googleapis.com/css2?family=Lato:wght@900&family=Open+Sans:wght@300;400&family=Montserrat:wght@800&display=swap">
<style>
  :root {
    --page-bg: #d6d6d6;
    --label-bg: #0d0e0e;
    --label-edge: #1c1d1d;
    --mandala-tone: #2a302d;
    --logo-grey: #8c8f92;
    --organic-green: #6cbf5a;
    --swiss-red: #e1242b;
    --text-light: #d9dadb;
  }
  * { margin: 0; padding: 0; box-sizing: border-box; }
  html, body { width: 1200px; height: 1001px; overflow: hidden; }
  body {
    background: var(--page-bg);
    display: flex;
    align-items: center;
    justify-content: center;
    font-family: "Open Sans", sans-serif;
  }
  .label {
    position: relative;
    width: 420px;
    height: 700px;
    background: var(--label-bg);
    border-radius: 6px;
    box-shadow: inset 0 0 0 1px var(--label-edge);
    overflow: hidden;
    padding: 60px 32px 0 30px;
  }
  .label__mandala {
    position: absolute;
    left: -60px;
    top: 90px;
    width: 540px;
    height: 540px;
    border-radius: 50%;
    background: radial-gradient(circle, var(--mandala-tone) 0%, rgba(42,48,45,0.35) 45%, rgba(13,14,14,0) 70%);
    opacity: 0.6;
  }
  .label__content { position: relative; }
  .brand-name {
    font-family: "Lato", sans-serif;
    font-weight: 900;
    font-size: 60px;
    letter-spacing: 5px;
    color: var(--logo-grey);
    line-height: 1;
  }
  .claim-row {
    margin-top: 128px;
    display: flex;
    align-items: center;
    gap: 6px;
  }
  .claim-row__organic {
    background: var(--organic-green);
    color: #f4f8f2;
    font-family: "Montserrat", sans-serif;
    font-weight: 800;
    font-size: 40px;
    line-height: 50px;
    padding: 0 6px;
    letter-spacing: 0.5px;
  }
  .claim-row__swiss {
    width: 50px;
    height: 50px;
    background: var(--swiss-red);
  }
  .product-name {
    margin-top: 8px;
    font-weight: 300;
    font-size: 58px;
    line-height: 1.1;
    color: var(--text-light);
  }
  .strength {
    margin-top: 70px;
    font-weight: 300;
    font-size: 42px;
    line-height: 1.35;
    color: var(--text-light);
  }
</style>
</head>
<body>
  <main class="label">
    <div class="label__mandala" role="img" aria-label="Faint mandala symbol decoration behind the label text"></div>
    <div class="label__content">
      <div class="brand-name">KELVORA</div>
      <div class="claim-row">
        <span class="claim-row__organic">ORGANIC</span>
        <span class="claim-row__swiss" role="img" aria-label="Swiss made badge"></span>
      </div>
      <h1 class="product-name">Cannabis Oil</h1>
      <p class="strength">500 mg CBD (5%)<br>Broad Spectrum</p>
    </div>
  </main>
</body>
</html>
```